RW Holloway LLC Business Card - Civil Engineering & Consulting Firm

We need a Business Card that is elegant, and masculine.  It is our Professional Civil Engineering & Consulting Company located in San Antonio TX (Not s construction or builder firm- no gears & no tool images please). We provide civil engineering services including  commercial site plans, grading and drainage plans, utility plans, hydraulics and hydrology, land planning, utility coordination, and other general civil engineering services related to commercial and residential development.
We have 2 existing Logos. We would like to convey reliability, strength, trustworthiness and attention to detail.  Blues and orange tones as per logo We are OK with the use of a darker blue in the mix.  We have 2 logo versions - Full Company Name Logo to go on the back of card, & Small Icon Logo for the front w/ personal Info.

Target Market(s)
Architects, Real Estate Developers, Other Strctural Engineers, Surveyers, General Contractors
Industry/Entity Type
Professional Civil Engineering
Contact Information for Business Card
Name, Position, Address, Cell & Office #, email, and company website
Font styles to use
Other font styles liked:
- Avian
Requirements
Should not have
- No Tools, No Gears, no Cranes, or Construction Equipment.

```html
<!DOCTYPE html>
<html lang="en">
<head>
<meta charset="utf-8">
<title>RW Holloway LLC – Business Card</title>
<link rel="stylesheet" href="https://fonts.googleapis.com/css2?family=Montserrat:wght@300;400;700&display=swap">
<style>
  :root {
    --bg: #c9c9c9;
    --paper: #ffffff;
    --ink: #1c1c1c;
    --orange: #ee8d2b;
    --blue: #7aa9d4;
    --steel: #7c9cb8;
    --amber: #d98e45;
    --white: #ffffff;
  }
  * { box-sizing: border-box; margin: 0; padding: 0; }
  html, body {
    width: 1200px; height: 813px; overflow: hidden;
    background: var(--bg);
    font-family: "Montserrat", Arial, sans-serif;
  }
  .stage {
    position: relative; width: 1200px; height: 813px;
    display: flex; align-items: center; justify-content: center; gap: 40px;
  }
  .card {
    position: relative; width: 540px; height: 309px;
    box-shadow: 0 10px 28px rgba(0,0,0,.28);
    overflow: hidden;
  }
  /* Front */
  .card--front { background: var(--paper); color: var(--ink); }
  .brand-mark {
    position: absolute; top: 36px; right: 36px;
    display: flex; align-items: center; gap: 10px;
  }
  .brand-mark__square { width: 18px; height: 18px; background: var(--blue); }
  .brand-mark__name {
    font-weight: 700; font-size: 17px; color: var(--orange); letter-spacing: .5px;
  }
  .accent-bar {
    position: absolute; left: 0; top: 120px; width: 22px; height: 40px;
    background: var(--orange);
  }
  .person { position: absolute; left: 42px; top: 118px; }
  .person__name {
    font-weight: 700; font-size: 19px; color: var(--orange);
    letter-spacing: 1px; text-transform: uppercase; line-height: 1.1;
  }
  .person__role { font-size: 14px; margin-top: 2px; }
  .address { position: absolute; left: 42px; top: 176px; font-size: 13px; line-height: 1.35; }
  .contacts { position: absolute; left: 42px; top: 218px; list-style: none; }
  .contacts li {
    display: flex; align-items: center; gap: 8px;
    font-size: 12.5px; line-height: 1.45;
  }
  .contacts svg { width: 12px; height: 12px; flex: none; }
  /* Back */
  .card--back {
    background: linear-gradient(160deg, var(--steel) 0%, #a3a09c 45%, var(--amber) 100%);
    color: var(--white);
    display: flex; flex-direction: column; align-items: center; justify-content: center;
  }
  .wordmark {
    font-weight: 300; font-size: 40px; letter-spacing: 4px; text-transform: uppercase;
  }
  .tagline {
    margin-top: 14px; font-weight: 300; font-size: 13px; letter-spacing: 7px;
    text-transform: uppercase;
  }
  .rule { width: 380px; height: 1.5px; background: var(--white); margin-top: 12px; }
</style>
</head>
<body>
<main class="stage">
  <section class="card card--front" aria-label="Card front">
    <div class="brand-mark">
      <span class="brand-mark__square"></span>
      <span class="brand-mark__name">RW Holloway LLC</span>
    </div>
    <span class="accent-bar"></span>
    <div class="person">
      <p class="person__name">Dana Whitfield</p>
      <p class="person__role">Co-Founder</p>
    </div>
    <p class="address">4180 Cedar Ridge Road<br>Suite 210 Alder Park</p>
    <ul class="contacts">
      <li><svg viewBox="0 0 12 12"><circle cx="6" cy="6" r="6" fill="var(--orange)"/><path d="M3.5 3.2l1.3-.4.7 1.6-.8.6a4 4 0 0 0 2.3 2.3l.6-.8 1.6.7-.4 1.3C6 8.6 3.4 6 3.5 3.2z" fill="#fff"/></svg>555-014-2231</li>
      <li><svg viewBox="0 0 12 12"><circle cx="6" cy="6" r="6" fill="var(--orange)"/><rect x="3" y="5" width="6" height="3.5" fill="#fff"/><rect x="2.5" y="3.4" width="7" height="1.2" fill="#fff"/></svg>555-014-7760</li>
      <li><svg viewBox="0 0 12 12"><circle cx="6" cy="6" r="6" fill="var(--orange)"/><rect x="2.8" y="3.8" width="6.4" height="4.4" fill="#fff"/><path d="M2.8 3.8L6 6.4l3.2-2.6" stroke="var(--orange)" stroke-width=".8" fill="none"/></svg>info@rwhollowayllc.com</li>
      <li><svg viewBox="0 0 12 12"><circle cx="6" cy="6" r="6" fill="var(--orange)"/><circle cx="6" cy="6" r="3.3" fill="none" stroke="#fff" stroke-width=".8"/><path d="M2.7 6h6.6M6 2.7v6.6" stroke="#fff" stroke-width=".8"/></svg>www.rwhollowayllc.com</li>
    </ul>
  </section>

  <section class="card card--back" aria-label="Card back">
    <p class="wordmark">RW Holloway LLC</p>
    <span class="rule"></span>
    <p class="tagline">Consulting Engineers</p>
  </section>
</main>
</body>
</html>
```